Business card design Needed for new logo / Construction business, home extensions and new builds

We need a business card design using our new logo files which i will attach to this project :)

We are a small construction business specialising in home extensions, new builds and property development. We are very ambitious and would appreciate professional and elegant designs for our new business card.

Very serious about using the services on MakerQuarry and recently acquired our new logo from here :)

Please get involved, i will feedback when i can as i am very busy but can respond daily, thanks

Target Market(s)

People that want to build onto their houses, new building developments or adding too their existing property

Industry/Entity Type

Construction

Contact Information for Business Card

Renwick Tolliver Construction, Lionel Ashby (Managing Director), Tel 07822254961, email - info@renwick-tolliver, www.renwick-tolliver.co.uk

Colors

Designer to choose colors to be used in the design.

Requirements
Must have
• I like a deep grey on the back please. A lot of you have provided black from and back, try mixing things up a little. The black looks cool 😎 Thanks

```html
<!DOCTYPE html>
<html lang="en">
<head>
<meta charset="utf-8">
<title>Renwick Tolliver Construction – Business Card</title>
<link rel="stylesheet" href="https://fonts.googleapis.com/css2?family=Arimo:wght@400;700&display=swap">
<style>
  :root {
    --page-bg: #2b2b2b;
    --deep-grey: #333334;
    --gold-light: #ecd08f;
    --gold-mid: #d4a850;
    --gold-dark: #b07e2a;
    --ink: #2e2c2a;
    --white: #f4f4f4;
  }
  * { box-sizing: border-box; margin: 0; padding: 0; }
  html, body {
    width: 1200px; height: 750px; overflow: hidden;
    background: var(--page-bg);
    font-family: "Arimo", Arial, sans-serif;
  }
  .stage {
    position: relative; width: 1200px; height: 750px;
    display: flex; align-items: center; justify-content: center; gap: 40px;
  }
  .card {
    position: relative; width: 520px; height: 298px;
    border-radius: 18px; overflow: hidden;
    box-shadow: 0 14px 30px rgba(0,0,0,.45);
  }
  /* Back side: deep grey */
  .card-back {
    background: var(--deep-grey);
    display: flex; flex-direction: column; align-items: center; justify-content: center;
  }
  .brand {
    display: flex; align-items: center; gap: 10px;
    color: var(--gold-mid); font-weight: 700; letter-spacing: .06em;
    text-transform: uppercase;
  }
  .brand-mark { width: 14px; height: 14px; background: var(--gold-mid); }
  .card-back .brand { font-size: 22px; text-align: center; flex-direction: column; gap: 14px; }
  .card-back .brand-mark { width: 22px; height: 22px; }
  .card-back .website {
    margin-top: 34px; color: var(--white); font-size: 14px; letter-spacing: .18em;
  }
  /* Front side: gold */
  .card-front {
    background: radial-gradient(ellipse at 55% 45%, var(--gold-light) 0%, var(--gold-mid) 50%, var(--gold-dark) 100%);
    color: var(--ink);
  }
  .card-front .brand {
    position: absolute; top: 34px; right: 34px;
    color: var(--ink); font-size: 13px;
  }
  .card-front .brand-mark { background: var(--ink); }
  .person { position: absolute; left: 36px; top: 164px; }
  .person-name { font-size: 24px; font-weight: 700; }
  .person-role { font-size: 14px; margin-top: 3px; }
  .rule-long {
    position: absolute; left: 230px; right: 26px; top: 198px;
    height: 1px; background: var(--ink);
  }
  .website-front {
    position: absolute; right: 30px; top: 178px; font-size: 12.5px;
  }
  .rule-short {
    position: absolute; left: 36px; width: 180px; top: 214px;
    height: 1px; background: var(--ink);
  }
  .contacts { position: absolute; left: 36px; top: 226px; list-style: none; font-size: 14px; }
  .contacts li { display: flex; align-items: center; gap: 8px; margin-bottom: 5px; }
  .contacts svg { width: 12px; height: 12px; fill: var(--ink); }
</style>
</head>
<body>
<main class="stage">
  <section class="card card-back">
    <div class="brand">
      <span class="brand-mark"></span>
      <span class="brand-name">Renwick Tolliver<br>Construction</span>
    </div>
    <p class="website">www.renwick-tolliver.co.uk</p>
  </section>

  <section class="card card-front">
    <div class="brand">
      <span class="brand-mark"></span>
      <span class="brand-name">Renwick Tolliver</span>
    </div>
    <div class="person">
      <h1 class="person-name">Lionel Ashby</h1>
      <p class="person-role">Managing Director</p>
    </div>
    <div class="rule-long"></div>
    <p class="website-front">www.renwick-tolliver.co.uk</p>
    <div class="rule-short"></div>
    <ul class="contacts">
      <li>
        <svg viewBox="0 0 24 24" aria-hidden="true"><path d="M6.6 10.8a15.1 15.1 0 0 0 6.6 6.6l2.2-2.2a1 1 0 0 1 1-.25 11.4 11.4 0 0 0 3.6.57 1 1 0 0 1 1 1V20a1 1 0 0 1-1 1A17 17 0 0 1 3 4a1 1 0 0 1 1-1h3.5a1 1 0 0 1 1 1c0 1.25.2 2.45.57 3.6a1 1 0 0 1-.25 1z"/></svg>
        07822254961
      </li>
      <li>
        <svg viewBox="0 0 24 24" aria-hidden="true"><path d="M2 5h20v14H2z M2 5l10 8 10-8" /></svg>
        info@renwick-tolliver
      </li>
    </ul>
  </section>
</main>
</body>
</html>
```